Web design - holistic filmmaker

I need a design for my new website.

I am a holistic filmmaker, ie I make films for healers, alternative practitioners, spiritual people and institutions that offer training in this field.

The design should be noble, bright, convey the feeling of space and expanse and have some particularly beautiful color accents.

The structure is: start page, offer, references, about me, imprint.

As an idea for the start page, I thought that either I could introduce myself as a filmmaker and my offer, or we could start right on the start page with the references, ie photos and links to already realized projects.

If you want more information or an exchange, I'd love to hear from you. At the moment I just don't know how to describe it better.

The winner will then be asked to design a logo.

Target Market(s)

healers, alternative practitioners, spiritual people and institutions that offer training in this field

Industry/Entity Type

Film production

Number of Pages Required

3 page

```html
<!DOCTYPE html>
<html lang="de">
<head>
<meta charset="utf-8">
<title>Marlo – Holistic Filmmaking</title>
<link rel="stylesheet" href="https://fonts.googleapis.com/css2?family=Roboto:wght@400;500;700;900&display=swap">
<style>
:root{
  --orange:#f3a95f;
  --peach:#f9d6b1;
  --ink:#222222;
  --text:#2b2b2b;
  --grey-bg:#f3f3f3;
  --black:#000000;
  --white:#ffffff;
  --tan-a:#dcae92;
  --tan-b:#a97c62;
}
*{margin:0;padding:0;box-sizing:border-box}
html,body{width:1200px;height:2987px;overflow:hidden}
body{position:relative;background:var(--white);font-family:'Roboto',Arial,sans-serif;color:var(--text)}
.abs{position:absolute}
.brand{font-family:'Roboto',Arial,sans-serif;font-weight:900;letter-spacing:-1px;line-height:1}
.site-header{left:0;top:0;width:1200px;height:109px;background:var(--white)}
.site-header .brand{left:97px;top:33px;font-size:40px;color:var(--ink)}
.main-nav a{position:absolute;top:45px;font-size:14px;color:var(--ink);text-decoration:none;letter-spacing:.2px}
.search-icon{left:1076px;top:42px}
.hero{left:0;top:109px;width:1200px;height:561px;
  background:radial-gradient(circle at 88% 62%,#ffd27a 0,#f29a2e 10%,#b9561c 28%,#4a2414 55%,#140b08 80%),#1a0f0b}
.hero-figure{left:330px;top:0;width:720px;height:561px;background:linear-gradient(180deg,rgba(10,6,5,.85),rgba(5,3,2,.95));border-radius:40% 40% 0 0/30% 30% 0 0;opacity:.75}
.hero .brand{left:95px;top:118px;font-size:138px;color:var(--white)}
.hero-text{left:97px;top:283px;width:440px;font-size:14px;line-height:26px;color:var(--white)}
.btn{display:block;background:var(--orange);color:var(--white);font-weight:700;font-size:13.5px;text-align:center;border-radius:4px;text-decoration:none;letter-spacing:.2px}
.hero .btn{left:97px;top:364px;width:119px;height:53px;line-height:53px}
.dots{left:577px;top:529px;display:flex;gap:6px}
.dots span{width:11px;height:11px;border-radius:50%;background:var(--white)}
.dots span.active{background:var(--orange)}
.band{left:0;width:1200px;height:76px}
.portrait-ring{left:99px;top:827px;width:432px;height:432px;border-radius:50%;background:var(--orange)}
.portrait{left:107px;top:827px;width:418px;height:418px;border-radius:50%;background:radial-gradient(circle at 50% 40%,#9a8a7c,#4a5a3c 60%,#26301f)}
h2{font-family:'Roboto',Arial,sans-serif;font-weight:700;color:var(--ink)}
.about h2{left:640px;top:828px;font-size:38px}
.body-text{font-size:14px;line-height:26.3px;color:var(--text);letter-spacing:-.05px}
.about .body-text{left:640px;top:903px;width:462px}
.about .btn{left:640px;top:1199px;width:126px;height:53px;line-height:53px}
.offer{left:0;top:1381px;width:1200px;height:524px;background:var(--grey-bg)}
.offer h2{left:97px;top:61px;font-size:38px}
.offer .body-text{left:97px;top:135px;width:462px}
.offer .btn{left:97px;top:403px;width:126px;height:53px;line-height:53px}
.offer-media{left:0;top:0}
.references h2{left:0;top:2016px;width:1200px;text-align:center;font-size:41px}
.ref-card{top:2111px;width:235px;height:266px}
.ref-card .play{position:absolute;left:85px;top:101px;width:64px;height:64px;border-radius:50%;background:rgba(255,255,255,.85)}
.ref-card .play svg{position:absolute;left:24px;top:20px}
.site-footer{left:0;top:2572px;width:1200px;height:415px;background:var(--black);color:var(--white)}
.site-footer .brand{left:102px;top:115px;font-size:58px;color:var(--white)}
.footer-nav{right:97px;top:134px;display:flex;gap:24px;font-size:13px}
.footer-nav a{color:var(--white);text-decoration:none}
.contact-icon{width:60px;height:60px;border-radius:50%;background:linear-gradient(160deg,var(--tan-a),var(--tan-b));top:232px;display:flex;align-items:center;justify-content:center}
.contact-label{top:242px;font-size:14.5px;font-weight:400}
.contact-value{top:266px;font-size:13px;line-height:22px}
.footer-rule{left:104px;top:332px;width:990px;height:1px;background:#3a3a3a}
.copyright{left:0;top:365px;width:1200px;text-align:center;font-size:14px}
</style>
</head>
<body>

<header class="abs site-header">
  <div class="abs brand">marlo</div>
  <nav class="main-nav">
    <a style="left:482px">HOME</a>
    <a style="left:577px">OFFER</a>
    <a style="left:673px">REFERENCES</a>
    <a style="left:816px">ABOUT ME</a>
    <a style="left:941px">IMPRINT</a>
  </nav>
  <svg class="abs search-icon" width="22" height="22" viewBox="0 0 22 22"><circle cx="9" cy="9" r="6.5" fill="none" stroke="var(--orange)" stroke-width="3"/><line x1="14" y1="14" x2="20" y2="20" stroke="var(--orange)" stroke-width="3.2" stroke-linecap="round"/></svg>
</header>

<section class="abs hero" role="img" aria-label="Silhouette of a woman holding a film clapperboard against a sunset sky">
  <div class="abs hero-figure"></div>
  <div class="abs brand">marlo</div>
  <p class="abs hero-text">Ende der 1990er Jahre stand ich vor der Frage, ob ich beruflich in die Al&shy;ternativmedizin oder in die Filmbranche gehen solle.</p>
  <a class="abs btn">WATCH NOW</a>
  <div class="abs dots"><span></span><span class="active"></span><span></span></div>
</section>

<svg class="abs band" style="top:670px" viewBox="0 0 1200 76" preserveAspectRatio="none">
  <polygon points="0,0 1200,0 1200,50 600,2 0,50" fill="var(--peach)"/>
  <polygon points="0,50 600,2 1200,50 1200,76 600,6 0,76" fill="var(--orange)"/>
</svg>

<section class="about">
  <div class="abs portrait-ring"></div>
  <div class="abs portrait" role="img" aria-label="Portrait photo of the filmmaker"></div>
  <h2 class="abs">About me</h2>
  <p class="abs body-text">Mein Name ist Marlo und ich mache Filme - mit Begeisterung und von ganzem Herzen. Ich bin ein holistischer Filmemacher. Ende der 1990er Jahre stand ich vor der Frage, ob ich beruflich in die Alterna&shy;tivmedizin oder in die Filmbranche gehen solle. Beruflich habe ich mich damals für den Film entschieden, aber das Geistig-Spirituelle und meine Leidenschaft für die sogenannten alternativen Heilmeth&shy;oden begleiten mich seitdem fast genauso intensiv. Mein filmischer Weg führte mich buchstäblich vom Kabelträger zum Kameramann, Regisseur und Produzenten. Angefangen hat alles 1995 als Kamer&shy;aassistent bei der amerikanischen Nachrichtenagentur NBX.</p>
  <a class="abs btn">LEARN MORE</a>
</section>

<section class="abs offer">
  <svg class="abs offer-media" width="1200" height="524" viewBox="0 0 1200 524">
    <defs>
      <radialGradient id="reelTone" cx="0.35" cy="0.4" r="0.8">
        <stop offset="0" stop-color="#b7a27e"/>
        <stop offset="0.45" stop-color="#6b4a2c"/>
        <stop offset="1" stop-color="#2a1a10"/>
      </radialGradient>
    </defs>
    <polygon points="635,0 645,0 593,524 573,524" fill="var(--orange)"/>
    <polygon points="643,0 1200,0 1200,524 591,524" fill="url(#reelTone)" role="img" aria-label="Vintage film reel on a wooden table"/>
  </svg>
  <h2 class="abs">Our offer</h2>
  <p class="abs body-text">Einen Film zu drehen ist immer auch eine Reise zu sich selbst. Mit einfachen Mitteln und ohne Spezialeffekte begleite ich Sie auf dem Weg, Ihr Wesen darzustellen. Ein dokumentarischer Werbefilm nah am Menschen. Filme mit Tiefgang richten sich an alle Menschen und Institutionen, deren Streben nach Wahrhaftigkeit die Triebfeder ihres Handelns ist. Hochwertige Bildgestaltung und die informative und verständliche Vermittlung komplexer Sachverhalte sind Leiden&shy;schaft und Grundlage meiner Imagefilme und Unternehmenspräsen&shy;tationen.</p>
  <a class="abs btn">LEARN MORE</a>
</section>

<section class="references">
  <h2 class="abs">Our References</h2>
  <div class="abs ref-card" style="left:98px;background:linear-gradient(180deg,#d8d2c6,#b44a86)" role="img" aria-label="Video still: woman in a pink sweater speaking">
    <div class="play"><svg width="20" height="24" viewBox="0 0 20 24"><polygon points="0,0 20,12 0,24" fill="var(--orange)"/></svg></div>
  </div>
  <div class="abs ref-card" style="left:355px;background:linear-gradient(180deg,#6d7a5a,#b8323f)" role="img" aria-label="Video still: practitioners during a healing session">
    <div class="play"><svg width="20" height="24" viewBox="0 0 20 24"><polygon points="0,0 20,12 0,24" fill="var(--orange)"/></svg></div>
  </div>
  <div class="abs ref-card" style="left:611px;background:linear-gradient(180deg,#4f7bb0,#2d2824)" role="img" aria-label="Video still: woman resting her head on her hand">
    <div class="play"><svg width="20" height="24" viewBox="0 0 20 24"><polygon points="0,0 20,12 0,24" fill="var(--orange)"/></svg></div>
  </div>
  <div class="abs ref-card" style="left:867px;background:linear-gradient(180deg,#7d8a5e,#3c3a30)" role="img" aria-label="Video still: man speaking at a lectern outdoors">
    <div class="play"><svg width="20" height="24" viewBox="0 0 20 24"><polygon points="0,0 20,12 0,24" fill="var(--orange)"/></svg></div>
  </div>
</section>

<svg class="abs band" style="top:2496px" viewBox="0 0 1200 76" preserveAspectRatio="none">
  <polygon points="0,0 600,70 1200,0 1200,26 600,74 0,26" fill="var(--orange)"/>
  <polygon points="0,26 600,74 1200,26 1200,76 0,76" fill="var(--peach)"/>
</svg>

<footer class="abs site-footer">
  <div class="abs brand">marlo</div>
  <nav class="abs footer-nav">
    <a>HOME</a><span>|</span><a>ABOUT ME</a><span>|</span><a>OFFER</a><span>|</span><a>REFERENCES</a><span>|</span><a>IMPRINT</a>
  </nav>

  <div class="abs contact-icon" style="left:169px">
    <svg width="16" height="22" viewBox="0 0 16 22"><path d="M8 0C3.6 0 0 3.5 0 7.8 0 13 8 22 8 22s8-9 8-14.2C16 3.5 12.4 0 8 0z" fill="var(--white)"/><circle cx="8" cy="8" r="3" fill="var(--tan-b)"/></svg>
  </div>
  <div class="abs contact-label" style="left:257px">ADDRESS :</div>
  <div class="abs contact-value" style="left:257px">Lorem ipsum dolor sit amet,<br>consectetur adipiscing</div>

  <div class="abs contact-icon" style="left:502px">
    <svg width="22" height="16" viewBox="0 0 22 16"><rect width="22" height="16" rx="2" fill="var(--white)"/><polyline points="1,2 11,9 21,2" fill="none" stroke="var(--tan-b)" stroke-width="1.8"/></svg>
  </div>
  <div class="abs contact-label" style="left:591px">EMAIL :</div>
  <div class="abs contact-value" style="left:591px">info@marlo-film.com</div>

  <div class="abs contact-icon" style="left:827px">
    <svg width="18" height="18" viewBox="0 0 24 24"><path d="M6.6 10.8c1.4 2.8 3.8 5.1 6.6 6.6l2.2-2.2c.3-.3.7-.4 1-.2 1.1.4 2.3.6 3.6.6.6 0 1 .4 1 1V20c0 .6-.4 1-1 1C10.6 21 3 13.4 3 4c0-.6.4-1 1-1h3.5c.6 0 1 .4 1 1 0 1.3.2 2.5.6 3.6.1.3 0 .7-.2 1L6.6 10.8z" fill="var(--white)"/></svg>
  </div>
  <div class="abs contact-label" style="left:916px">CALL US :</div>
  <div class="abs contact-value" style="left:916px">+1 (555) 010 2040</div>

  <div class="abs footer-rule"></div>
  <div class="abs copyright">© 2023 Marlo. All Rights Reserved</div>
</footer>

</body>
</html>
```